Ductless Mini Split Business Website

Copper Fern Services is looking to design an eye catching educational website about installing Ductless mini splits.

Similar to this company.
https://www.halvikstream.com/

Coding

Coded - Design and coding required

```html
<!DOCTYPE html>
<html lang="en">
<head>
<meta charset="utf-8">
<title>Reviews | Copper Fern Services</title>
<link href="https://fonts.googleapis.com/css2?family=Heebo:wght@300;400;500&display=swap" rel="stylesheet">
<style>
  :root {
    --yellow: #f8c40d;
    --yellow-soft: #fefac9;
    --ink: #222222;
    --body: #666666;
    --muted: #888888;
    --white: #ffffff;
    --shadow: 0 6px 30px rgba(60, 90, 140, 0.10);
  }
  * { margin: 0; padding: 0; box-sizing: border-box; }
  html, body { width: 1200px; height: 2284px; overflow: hidden; background: var(--white); }
  body { position: relative; font-family: "Heebo", sans-serif; color: var(--ink); }
  .abs { position: absolute; }
  .backdrop { position: absolute; left: 0; top: 0; width: 1200px; height: 2284px; z-index: 0; }

  .brand { left: 38px; top: 22px; display: flex; align-items: center; gap: 8px; z-index: 2; }
  .brand-dot { width: 22px; height: 22px; border-radius: 50%; background: var(--yellow); }
  .brand-name { font-size: 17px; font-weight: 500; color: var(--ink); line-height: 1; }

  .nav { top: 34px; z-index: 2; display: flex; font-size: 15px; font-weight: 400; color: #333; }
  .nav a { position: absolute; white-space: nowrap; color: inherit; text-decoration: none; }
  .nav .active::after { content: ""; position: absolute; left: 0; right: 0; top: 24px; height: 2px; background: var(--yellow); }
  .caret { font-size: 10px; margin-left: 3px; color: #777; }

  .page-title { left: 107px; top: 164px; font-size: 53px; font-weight: 500; z-index: 2; }
  .crumbs { left: 107px; top: 235px; font-size: 15px; z-index: 2; display: flex; align-items: center; gap: 6px; }
  .crumbs .current { color: var(--muted); }

  .intro-title { left: 107px; top: 366px; font-size: 41px; font-weight: 400; z-index: 2; }
  .intro-text { left: 107px; top: 436px; width: 565px; font-size: 13.5px; font-weight: 300; line-height: 28.5px; color: var(--body); z-index: 2; }
  .intro-text p + p { margin-top: 13px; }
  .intro-photo { left: 698px; top: 391px; width: 396px; height: 263px; background: linear-gradient(120deg, #276a80 0%, #1b4b5e 55%, #0f2630 100%); z-index: 2; }

  .review { width: 480px; height: 261px; background: var(--white); box-shadow: var(--shadow); padding: 42px 36px 0; z-index: 2; }
  .review.photo-card { background: linear-gradient(135deg, #f7f5f2 0%, #eeece8 60%, #e6e3de 100%); }
  .review-date { display: flex; align-items: baseline; gap: 8px; }
  .review-day { font-size: 32px; font-weight: 300; color: var(--yellow); line-height: 1; }
  .review-month { font-size: 14px; color: var(--muted); }
  .review-text { margin-top: 14px; font-size: 18px; font-weight: 400; line-height: 25px; color: var(--ink); }
  .review-foot { position: absolute; left: 36px; top: 200px; display: flex; align-items: center; gap: 18px; font-size: 14px; }
  .stars { display: flex; gap: 3px; }

  .load-more { left: 531px; top: 1805px; width: 138px; height: 41px; border-radius: 21px; background: var(--yellow); color: var(--white); font-size: 14px; font-weight: 500; display: flex; align-items: center; justify-content: center; box-shadow: 0 10px 24px rgba(90,120,200,0.15); z-index: 2; }

  .divider { left: 107px; top: 1918px; width: 986px; height: 1px; background: #fbeeb4; z-index: 2; }

  .foot-col { top: 1984px; z-index: 2; }
  .foot-col h3 { font-size: 22px; font-weight: 400; margin-bottom: 14px; }
  .foot-col ul { list-style: none; }
  .foot-col li { font-size: 14px; font-weight: 300; color: var(--body); height: 34.7px; }
  .foot-col .addr { font-size: 14px; font-weight: 300; color: var(--body); line-height: 28.5px; margin-top: -4px; }
  .foot-col .phone { font-size: 25px; font-weight: 300; color: var(--yellow); margin-top: 8px; }
  .foot-col .about { font-size: 14px; font-weight: 300; color: var(--body); line-height: 28.5px; width: 310px; margin-top: -4px; }
  .socials { display: flex; gap: 7px; margin-top: 10px; }
  .socials span { width: 36px; height: 36px; border-radius: 50%; }

  .to-top { left: 1111px; top: 2194px; width: 44px; height: 44px; border-radius: 50%; background: var(--yellow); display: flex; align-items: center; justify-content: center; box-shadow: 0 6px 18px rgba(248,196,13,0.35); z-index: 2; }
  .copyright { left: 93px; top: 2238px; font-size: 12px; color: #333; z-index: 2; }
</style>
</head>
<body>

<svg class="backdrop" viewBox="0 0 1200 2284" aria-hidden="true">
  <path d="M250 0 H1200 V95 L580 228 Q540 236 500 214 L262 78 Q232 58 238 22 Z" fill="#fefac9"/>
  <path d="M0 756 L329 1138 L0 1520 Z" fill="#fefac9"/>
</svg>

<div class="abs brand"><span class="brand-dot"></span><span class="brand-name">Copper Fern Services</span></div>

<nav class="abs nav" style="left:0;">
  <a style="left:364px;">Home</a>
  <a style="left:432px;">About<span class="caret">&#8964;</span></a>
  <a style="left:515px;">Ductless Heat Pumps<span class="caret">&#8964;</span></a>
  <a style="left:707px;">Ductless Heat Pumps FAQ</a>
  <a style="left:917px;">Financing</a>
  <a class="active" style="left:1013px;">Reviews</a>
  <a style="left:1095px;">Contact</a>
</nav>

<h1 class="abs page-title">Reviews</h1>
<div class="abs crumbs">
  <svg width="13" height="12" viewBox="0 0 13 12"><path d="M6.5 0 L13 6 H11 V12 H8 V8 H5 V12 H2 V6 H0 Z" fill="#333"/></svg>
  <span>Home</span><span class="current">&rsaquo;</span><span class="current">Reviews</span>
</div>

<h2 class="abs intro-title">Let Our Reviews Speak</h2>
<div class="abs intro-text">
  <p>Copper Fern Serives is looking forward to providing you with the high-performing, energy-efficient ductless system you deserve. Our technicians are also ready for any services your existing ductless system might need. From repair and maintenance to baseboard heating replacement and new installation, we are your trusted experts. But don’t just take our word for it. See what our past customers are saying about us in the reviews below.</p>
  <p>After serving your home, please take the time to leave a review for us too. Your feedback not only helps other customers but also gives us the opportunity to improve our service further.</p>
</div>
<div class="abs intro-photo" role="img" aria-label="Photo of a hand placing the fifth gold star in a row of five-star ratings on a dark teal background"></div>

<svg width="0" height="0" style="position:absolute">
  <defs><path id="star" d="M8 0 L10.2 5.2 L16 5.6 L11.6 9.3 L13 15 L8 12 L3 15 L4.4 9.3 L0 5.6 L5.8 5.2 Z" fill="#f8c40d"/></defs>
</svg>

<article class="abs review" style="left:107px; top:804px;">
  <div class="review-date"><span class="review-day">23</span><span class="review-month">October, 2019</span></div>
  <p class="review-text">Copper Fern is an amazing company and takes care of its customers! I would recommend them to anyone looking for a new system.</p>
  <div class="review-foot"><span>- Owen R</span><span class="stars"><svg width="16" height="15"><use href="#star"/></svg><svg width="16" height="15"><use href="#star"/></svg><svg width="16" height="15"><use href="#star"/></svg><svg width="16" height="15"><use href="#star"/></svg><svg width="16" height="15"><use href="#star"/></svg></span></div>
</article>

<article class="abs review" style="left:613px; top:804px;">
  <div class="review-date"><span class="review-day">13</span><span class="review-month">August, 2019</span></div>
  <p class="review-text">Fantastic company! My experience with Devon was great. Installation was quick and easy, highly recommend!</p>
  <div class="review-foot"><span>- Marisol</span><span class="stars"><svg width="16" height="15"><use href="#star"/></svg><svg width="16" height="15"><use href="#star"/></svg><svg width="16" height="15"><use href="#star"/></svg><svg width="16" height="15"><use href="#star"/></svg><svg width="16" height="15"><use href="#star"/></svg></span></div>
</article>

<article class="abs review photo-card" style="left:107px; top:1138px;" role="img" aria-label="Review card over a faint photo of a bright white living room interior">
  <div class="review-date"><span class="review-day">08</span><span class="review-month">July, 2019</span></div>
  <p class="review-text">I have been incredibly impressed with Copper Fern Services. They gave me a fair estimate with awesome rebates.</p>
  <div class="review-foot"><span>- Brianna</span><span class="stars"><svg width="16" height="15"><use href="#star"/></svg><svg width="16" height="15"><use href="#star"/></svg><svg width="16" height="15"><use href="#star"/></svg><svg width="16" height="15"><use href="#star"/></svg><svg width="16" height="15"><use href="#star"/></svg></span></div>
</article>

<article class="abs review" style="left:613px; top:1138px;">
  <div class="review-date"><span class="review-day">14</span><span class="review-month">April, 2019</span></div>
  <p class="review-text">Everything was straightforward, great scheduling, and the installers were super knowledgeable about the product.</p>
  <div class="review-foot"><span>- Nora K</span><span class="stars"><svg width="16" height="15"><use href="#star"/></svg><svg width="16" height="15"><use href="#star"/></svg><svg width="16" height="15"><use href="#star"/></svg><svg width="16" height="15"><use href="#star"/></svg><svg width="16" height="15"><use href="#star"/></svg></span></div>
</article>

<article class="abs review" style="left:107px; top:1471px;">
  <div class="review-date"><span class="review-day">13</span><span class="review-month">December, 2018</span></div>
  <p class="review-text">Oh, my gosh! These guys are awesome. They do good work, use good products, and the incentives are great and Supportive!</p>
  <div class="review-foot"><span>- Samuel Price</span><span class="stars"><svg width="16" height="15"><use href="#star"/></svg><svg width="16" height="15"><use href="#star"/></svg><svg width="16" height="15"><use href="#star"/></svg><svg width="16" height="15"><use href="#star"/></svg><svg width="16" height="15"><use href="#star"/></svg></span></div>
</article>

<article class="abs review" style="left:613px; top:1471px;">
  <div class="review-date"><span class="review-day">08</span><span class="review-month">July, 2018</span></div>
  <p class="review-text">Copper Fern Ductless did FANTASTIC work installing a new ductless heat pump for my customer and highly recommending them.</p>
  <div class="review-foot"><span>- Colin W</span><span class="stars"><svg width="16" height="15"><use href="#star"/></svg><svg width="16" height="15"><use href="#star"/></svg><svg width="16" height="15"><use href="#star"/></svg><svg width="16" height="15"><use href="#star"/></svg><svg width="16" height="15"><use href="#star"/></svg></span></div>
</article>

<div class="abs load-more">Load More</div>

<div class="abs divider"></div>

<section class="abs foot-col" style="left:107px;">
  <h3>Location</h3>
  <p class="addr">2875 NW Larchmont Road,<br>Suite B214<br>Danforth, OR 97305</p>
  <p class="phone">(503) 555-0187</p>
</section>
<section class="abs foot-col" style="left:360px;">
  <h3>Copper Fern Services</h3>
  <ul><li>Home</li><li>About</li><li>Ductless Heat Pumps</li><li>Ductless Heat Pumps FAQ</li></ul>
</section>
<section class="abs foot-col" style="left:613px;">
  <h3>Quick Link</h3>
  <ul><li>Financing</li><li>Contact Us</li><li>Privacy Policy</li><li>Sitemap</li></ul>
</section>
<section class="abs foot-col" style="left:782px;">
  <h3>About Us</h3>
  <p class="about">Experience maximum comfort, better indoor air quality, and lower utility bills by installing ductless heat pumps in your home.</p>
  <div class="socials">
    <span style="background:#4a64b0;"></span>
    <span style="background:#d8232a;"></span>
    <span style="background:#f8c40d;"></span>
    <span style="background:#e0141e;"></span>
  </div>
</section>

<div class="abs to-top"><svg width="16" height="10" viewBox="0 0 16 10"><path d="M2 8 L8 2 L14 8" stroke="#fff" stroke-width="2.4" fill="none" stroke-linecap="round" stroke-linejoin="round"/></svg></div>

<p class="abs copyright">Copyright ©2019 | All rights reserved</p>

</body>
</html>
```